Business Card Design Project

I need a business card designed from scratch. I have an existing logo that I can upload in Illustrator for modification or redesign.

The Company is called Query Lanterns http://querylanterns.com.au and we provide Search Engine Optimization services to Australian businesses. The current logo signifies an increase in visitors, profits etc...

There are no restrictions as to the redesign - colours, style etc are all open to change.

Cards will be full colour and one sided printed at http://www.cardmoxel.com.au so check their requirements for file format and sizes etc.

I will expect all original files upon completion of project.

Target Market(s)

Any business with a web site looking to improve their search engine rankings

Industry/Entity Type

Business

Requirements
Must have
• I like modern, sleek designs. Clean, not fussy, uncluttered.

```html
<!DOCTYPE html>
<html lang="en">
<head>
<meta charset="utf-8">
<title>Query Lanterns — Business Card</title>
<link rel="stylesheet" href="https://fonts.googleapis.com/css2?family=Open+Sans:wght@400;600;700;800&display=swap">
<style>
  :root {
    --brand-blue: #1874bd;
    --brand-yellow: #f6c515;
    --ink: #3a3a3a;
    --card-white: #ffffff;
    --backdrop: #ecebe8;
  }
  * { box-sizing: border-box; margin: 0; padding: 0; }
  html, body {
    width: 1200px; height: 460px; overflow: hidden;
    background: var(--backdrop);
    font-family: "Open Sans", Arial, sans-serif;
  }
  .card {
    position: absolute; top: 76px;
    width: 542px; height: 308px;
    border-radius: 14px;
    overflow: hidden;
    box-shadow: 0 3px 8px rgba(0,0,0,.18);
  }
  .card--front { left: 47px; background: var(--card-white); }
  .card--back { left: 612px; background: var(--brand-blue); }

  .wordmark {
    position: absolute; display: flex; align-items: center; gap: 12px;
    font-weight: 800; letter-spacing: .5px; white-space: nowrap;
  }
  .wordmark__dot { width: 18px; height: 18px; border-radius: 50%; }
  .card--front .wordmark { left: 0; right: 0; top: 76px; justify-content: center; color: var(--brand-blue); font-size: 40px; }
  .card--front .wordmark__dot { background: var(--brand-blue); }
  .card--back .wordmark { left: 0; right: 0; top: 118px; justify-content: center; color: #fff; font-size: 40px; }
  .card--back .wordmark__dot { background: #fff; }

  .name-band {
    position: absolute; left: 0; right: 0; top: 198px; height: 30px;
    background: var(--brand-blue);
    color: #fff; display: flex; align-items: center; justify-content: center; gap: 6px;
  }
  .name-band__accent { position: absolute; left: 0; top: 0; }
  .name-band__name { font-weight: 700; font-size: 16px; }
  .name-band__title { font-size: 13px; }

  .contacts {
    position: absolute; left: 24px; top: 240px;
    display: grid; grid-template-columns: 168px 108px auto; row-gap: 4px;
    font-size: 12.5px; color: var(--ink); line-height: 17px;
  }
  .contact { display: flex; align-items: center; gap: 5px; white-space: nowrap; }
  .contact svg { width: 10px; height: 10px; fill: var(--brand-blue); flex: none; }

  .web-address {
    position: absolute; left: 0; right: 0; top: 198px; text-align: center;
    color: #fff; font-size: 13px; letter-spacing: 2.2px;
  }
</style>
</head>
<body>
  <section class="card card--front">
    <div class="wordmark"><span class="wordmark__dot"></span>QUERY LANTERNS</div>

    <div class="name-band">
      <svg class="name-band__accent" width="40" height="30" viewBox="0 0 40 30" aria-hidden="true">
        <polygon points="0,0 40,0 28,30 0,30" fill="var(--brand-yellow)"/>
      </svg>
      <span class="name-band__name">Your Name</span><span class="name-band__title">Title</span>
    </div>

    <div class="contacts">
      <span class="contact">00Floor Street, City Name</span>
      <span class="contact"><svg viewBox="0 0 10 10"><path d="M2 0h2l1 3-1.5 1a6 6 0 0 0 2.5 2.5L7 5l3 1v2a2 2 0 0 1-2 2A8 8 0 0 1 0 2a2 2 0 0 1 2-2z"/></svg>012 345 6789</span>
      <span class="contact"><svg viewBox="0 0 10 10"><path d="M0 2h10v6H0z M0 2l5 3 5-3" /></svg>enquiry@querylanterns.com.au</span>
      <span class="contact">State Name, Contry Name</span>
      <span class="contact"><svg viewBox="0 0 10 10"><rect x="2" y="0" width="6" height="10" rx="1"/></svg>012 345 6789</span>
      <span class="contact"><svg viewBox="0 0 10 10"><circle cx="5" cy="5" r="4.5"/></svg>www.querylanterns.com.au</span>
    </div>
  </section>

  <section class="card card--back">
    <div class="wordmark"><span class="wordmark__dot"></span>QUERY LANTERNS</div>
    <p class="web-address">www.querylanterns.com.au</p>
  </section>
</body>
</html>
```